4D Cradle Glimpse Luxury Ultrasound Billboard

Design a HIGH-END, MODERN billboard for my private prenatal ultrasound studio, 4D Cradle Glimpse, located in Pace, Florida.
This billboard will be viewed by drivers traveling at highway speeds, so it must be extremely clean, simple, and readable within 6 seconds.
About My Business
4D Cradle Glimpse is a private prenatal ultrasound studio specializing in:
Highest technology 4D/HD Ultrasounds
Early Gender Determination
Pregnancy Confirmation
I have been serving families for nearly 10 years and is known for creating a memorable experience, not just an ultrasound appointment.
Design Style
I DO NOT want:
Flowers
Leaves
Swirls
Glitter
Hearts everywhere
Busy backgrounds
Generic maternity stock graphics
I DO want:
Modern
Luxury
Upscale
Clean
Professional
Eye-catching
Premium medical spa feel
Colors
Use colors from my logo:
LOGO Green ( or a deep green)
Black
White
Soft Gold accents
Images:
Incorporate my professional headshot in a clean, modern way, logo, and the ultrasound images
Text
Keep wording minimal.
Primary Headline ( OPEN TO IDEAS) :
EXAMPLES ( WOULD RATHER SOMETHING MORE CATCHY)
" ADVANCED IMAGING. UNFORGETTABLE MOMENTS"
"MEET YOUR BABY BEFORE BIRTH"
Under headline:
4D Ultrasound • Early Gender • Pregnancy Confirmation
Business Name:
4D Cradle Glimpse
Private Prenatal Ultrasound Studio
Phone Number:
850-471-5923
Important
This billboard must be readable in 5–6 seconds from a moving vehicle.
Less text is better.
The phone number and business name must be visible from a distance.
The design should feel like a premium brand that immediately tells expecting parents:
“This is where I go to see my baby.”
Files Provided
Official logo
Headshot
Ultrasound images
Don’t make this look like a medical office billboard.
Make it look like a luxury baby experience billboard. That’s what separates 4D Cradle Glimpse from hospitals, OB offices, and all the new studios popping up around you. The emotional connection is what gets moms to book. ❤️
Billboard Size - 10.6” x 36”

```html
<!DOCTYPE html>
<html lang="en">
<head>
<meta charset="utf-8">
<title>4D Cradle Glimpse Billboard</title>
<link rel="stylesheet" href="https://fonts.googleapis.com/css2?family=Playfair+Display:wght@700&family=Poppins:wght@500;600;700&family=Nunito+Sans:wght@800&family=Kaushan+Script&display=swap">
<style>
  :root {
    --page: #c4c4c4;
    --cream: #f5efe6;
    --forest: #2c3530;
    --ink: #2a302c;
    --gold: #c9a23a;
    --gold-soft: #d8bb6a;
    --white: #ffffff;
    --slate: #5e6b66;
    --rule: #cfc6b6;
  }
  * { margin: 0; padding: 0; box-sizing: border-box; }
  html, body { width: 1105px; height: 1200px; overflow: hidden; background: var(--page); }
  .billboard {
    position: absolute; left: 20px; top: 334px;
    width: 1065px; height: 531px;
    background: var(--cream); overflow: hidden;
    font-family: "Poppins", sans-serif;
  }
  .headshot {
    position: absolute; left: 22px; top: 21px; width: 257px; height: 370px;
    border-radius: 110px 110px 8px 8px;
    background: linear-gradient(180deg, #d9b98a 0%, #c99a79 35%, #3b5a3a 62%, #2f4a30 100%);
  }
  .scan-frame { position: absolute; left: 0; top: 0; width: 1065px; height: 405px; }
  .footer-band {
    position: absolute; left: 0; top: 405px; width: 1065px; height: 126px;
    background: var(--forest); border-top: 3px solid var(--gold);
  }
  .brand-box {
    position: absolute; left: 34px; top: 386px; width: 241px; height: 122px;
    background: var(--white); border: 2px solid #9aa39f; border-radius: 16px;
    display: flex; flex-direction: column; align-items: center; justify-content: center; gap: 8px;
  }
  .brand-name {
    font-family: "Playfair Display", serif; font-weight: 700; color: var(--gold);
    font-size: 25px; line-height: 1.1; text-align: center;
  }
  .brand-rule { width: 200px; height: 1px; background: var(--gold-soft); }
  .brand-tag { font-size: 9.5px; font-weight: 500; color: var(--slate); letter-spacing: 0.6px; }
  .headline { position: absolute; left: 320px; width: 344px; top: 0; text-align: center; }
  .headline-kicker {
    position: absolute; left: -10px; right: -10px; top: 50px;
    font-size: 31px; font-weight: 500; line-height: 1; color: var(--ink);
    letter-spacing: 17px; padding-left: 17px;
  }
  .headline-main {
    position: absolute; left: -20px; right: -20px; top: 74px;
    font-family: "Playfair Display", serif; font-weight: 700; font-size: 118px; line-height: 1;
    color: var(--gold); letter-spacing: 8px; padding-left: 8px;
  }
  .headline-sub {
    position: absolute; left: -10px; right: -10px; top: 183px;
    font-family: "Nunito Sans", sans-serif; font-weight: 800; font-size: 46px; line-height: 1;
    color: var(--ink); letter-spacing: -0.5px;
  }
  .divider {
    position: absolute; left: 325px; top: 259px; width: 334px; height: 1px;
    background: var(--gold-soft);
  }
  .services { position: absolute; left: 300px; top: 293px; width: 390px; height: 80px; }
  .service { position: absolute; top: 0; width: 130px; text-align: center; }
  .service-icon {
    width: 49px; height: 49px; margin: 0 auto; border-radius: 50%;
    background: var(--gold); display: flex; align-items: center; justify-content: center;
  }
  .service-label {
    margin-top: 9px; font-size: 12.5px; font-weight: 600; color: var(--ink); line-height: 1.05;
    white-space: nowrap;
  }
  .service-sep { position: absolute; top: 8px; width: 1px; height: 62px; background: var(--rule); }
  .phone-icon {
    position: absolute; left: 318px; top: 448px; width: 45px; height: 45px;
    border: 1.5px solid var(--gold); border-radius: 50%;
    display: flex; align-items: center; justify-content: center;
  }
  .phone-number {
    position: absolute; left: 376px; top: 438px;
    font-size: 47px; font-weight: 600; color: var(--white); letter-spacing: 1px; line-height: 1.4;
  }
  .band-sep { position: absolute; left: 762px; top: 448px; width: 1px; height: 46px; background: #8d958f; }
  .motto { position: absolute; left: 790px; width: 256px; top: 437px; text-align: center; color: var(--white); }
  .motto-script { font-family: "Kaushan Script", cursive; font-size: 27px; line-height: 1.1; }
  .motto-caps { font-size: 21px; font-weight: 500; letter-spacing: 0.5px; line-height: 1.3; }
</style>
</head>
<body>
<main class="billboard">
  <svg class="scan-frame" viewBox="0 0 1065 405" width="1065" height="405">
    <defs>
      <linearGradient id="scanTone" x1="0" y1="0" x2="0" y2="1">
        <stop offset="0" stop-color="#b06a4e"/>
        <stop offset="0.4" stop-color="#9a5a40"/>
        <stop offset="0.5" stop-color="#1a1512"/>
        <stop offset="0.6" stop-color="#9c5c42"/>
        <stop offset="1" stop-color="#b36d51"/>
      </linearGradient>
    </defs>
    <circle cx="941" cy="201" r="241" fill="url(#scanTone)" stroke="var(--gold)" stroke-width="5" role="img" aria-label="4D ultrasound image of twin babies face to face"/>
  </svg>

  <div class="headshot" role="img" aria-label="Portrait of the studio owner in green scrubs holding an ultrasound probe"></div>

  <section class="headline">
    <div class="headline-kicker">MEET YOUR</div>
    <div class="headline-main">BABY</div>
    <div class="headline-sub">BEFORE BIRTH</div>
  </section>

  <div class="divider"></div>

  <section class="services">
    <div class="service" style="left:0">
      <div class="service-icon">
        <svg width="26" height="26" viewBox="0 0 26 26" fill="none" stroke="#fff" stroke-width="1.6" stroke-linecap="round">
          <path d="M8 6 a7 7 0 0 1 10 0"/><path d="M10 9 a4 4 0 0 1 6 0"/>
          <path d="M9 12 h8 l-1 5 a3 3 0 0 1 -6 0 z"/><path d="M13 20 v4"/>
        </svg>
      </div>
      <div class="service-label">4D ULTRASOUND</div>
    </div>
    <div class="service-sep" style="left:132px"></div>
    <div class="service" style="left:130px">
      <div class="service-icon">
        <svg width="28" height="28" viewBox="0 0 28 28" fill="none" stroke="#fff" stroke-width="1.6" stroke-linecap="round">
          <circle cx="10" cy="12" r="5"/><path d="M10 17 v7 M7 21 h6"/>
          <circle cx="16" cy="12" r="5"/><path d="M20 8 l5 -5 M21 3 h4 v4"/>
        </svg>
      </div>
      <div class="service-label">EARLY GENDER</div>
    </div>
    <div class="service-sep" style="left:259px"></div>
    <div class="service" style="left:260px">
      <div class="service-icon">
        <svg width="22" height="22" viewBox="0 0 22 22" fill="none" stroke="#fff" stroke-width="2.6" stroke-linecap="round" stroke-linejoin="round">
          <path d="M5 11 l4 4 l8 -9"/>
        </svg>
      </div>
      <div class="service-label">PREGNANCY<br>CONFIRMATION</div>
    </div>
  </section>

  <div class="footer-band"></div>

  <div class="brand-box">
    <div class="brand-name">4D Cradle Glimpse</div>
    <div class="brand-rule"></div>
    <div class="brand-tag">PRENATAL ULTRASOUND STUDIO</div>
  </div>

  <div class="phone-icon">
    <svg width="22" height="22" viewBox="0 0 24 24" fill="var(--gold)">
      <path d="M6.6 10.8a15.1 15.1 0 0 0 6.6 6.6l2.2-2.2a1 1 0 0 1 1-.25 11.4 11.4 0 0 0 3.6.57 1 1 0 0 1 1 1V20a1 1 0 0 1-1 1A17 17 0 0 1 3 4a1 1 0 0 1 1-1h3.5a1 1 0 0 1 1 1c0 1.25.2 2.45.57 3.57a1 1 0 0 1-.25 1z"/>
    </svg>
  </div>
  <div class="phone-number">850-471-5923</div>
  <div class="band-sep"></div>
  <div class="motto">
    <div class="motto-script">Precious moments</div>
    <div class="motto-caps">LIFETIME MEMORIES</div>
  </div>
</main>
</body>
</html>
```